Website Creation for Kesto Course 2025 by Lon Varick "The Girl Who Painted Her Sky"

Project Title: "Kesto" Course Design Brief – Website design Build on Tilda
Client: Pebble Lantern Education
Course Title: Kesto by Lon Varick – The Girl Who Painted Her Sky
Logo: Lon Varick Logo
Course price: TBA
Overview:
We are seeking a designer to create cohesive and professional design assets for a new online course called Kesto. This transformative program combines neuroscience, emotional wellness, and ancient meditation practices to guide users through a journey of self-healing. We want the design to feel scientific yet spiritual, with clean, modern aesthetics that also convey depth and transformation. We use Tilda as our website builder so we need a design that can be easily transposed to that platform.
We require a visually compelling and dynamic banner image for the course webpage hero section (desktop and mobile versions)
We also require 7 x Individual thumbnail designs for each chakra meditation that will accompany the course with a workbook that will be designed in house (aligned with energy centre themes / Solfeggio frequencies / cosmic and sacred geometry)
Visual Direction:
• Clean, modern design with dark elements that balance science and spirituality.
• Soft gradients, energetic colors for chakras, and subtle abstract patterns or sacred geometry.
• Imagery could include brain neural networks, energy centres, or serene meditative figures and sacred geometry.
Course Themes to Inspire Design:
• Neuroplasticity and brain rewiring
• Emotional trauma and healing
• Meditation and Solfeggio frequencies
• Mind-body-spirit connection
• Empowerment and transformation
Lesson Breakdown:
• Lesson 1: The Science of Meditation & the Mind-Body Connection
• Lesson 2: Lon Varick’s Personal Healing & Neuroplasticity
• Lesson 3: Emotional Stress and Disease
• Lesson 4: ZRM (Zonal Ribbon Merge) Process
• Lesson 5: Solfeggio Frequencies & Chakra Healing
Target Audience:
Adult women 40 to 60 years old interested in healing illness, improving mental health, improving relationships, improving personal development, alternative healing, and meditation.

self development, meditation, healing

1 page

• futurapt

• branding copy used with relevant imagery and brand colours Stone #FAF0EA Sand #E2B9A5 Steel Blue #4F5266 Navy #2B243A Black: #000000 and Futura PT font
• chakra symbols and cosmic aesthetics with informational psychographics
• bright bold colours that don't match our branding

```html
<!DOCTYPE html>
<html lang="en">
<head>
<meta charset="utf-8">
<title>Kesto by Lon Varick – The Girl Who Painted Her Sky</title>
<link rel="stylesheet" href="https://fonts.googleapis.com/css2?family=Poppins:wght@400;500;600&family=Roboto:wght@400;500;700&display=swap">
<style>
  :root {
    --green: #8fcc3f;
    --green-band: #95d04a;
    --blue: #0b8fe6;
    --blue-deep: #0577d0;
    --ink: #111111;
    --body-grey: #555a60;
    --white: #ffffff;
    --hero-dark: #1d1a1c;
    --map-green: #cdeedd;
    --map-light: #eef3ee;
    --footer: #050505;
    --symbol-fill: rgba(255,255,255,0.16);
  }
  * { box-sizing: border-box; margin: 0; padding: 0; }
  html, body { width: 1200px; height: 3386px; overflow: hidden; }
  body { position: relative; font-family: "Roboto", Arial, sans-serif; color: var(--ink); background: var(--white); }
  .abs { position: absolute; }
  .heading { font-family: "Poppins", "Futura", sans-serif; font-weight: 500; text-transform: uppercase; letter-spacing: 0.2px; }
  .dots { position: absolute; width: 94px; height: 4px;
    background: radial-gradient(circle, currentColor 1.4px, transparent 1.6px) 0 0 / 9.4px 4px repeat-x; }

  /* Hero */
  .hero { position: absolute; left: 0; top: 0; width: 1200px; height: 640px; overflow: hidden;
    background: radial-gradient(ellipse 420px 380px at 600px 300px, #7a5c44 0%, #46372d 45%, var(--hero-dark) 100%); }
  .hero-photo { position: absolute; inset: 0; }
  .brand { position: absolute; left: 142px; top: 52px; display: flex; align-items: center; gap: 10px;
    font-family: "Poppins", sans-serif; font-size: 12px; letter-spacing: 3px; color: var(--white); font-weight: 500; }
  .brand-dot { width: 14px; height: 14px; border: 1.5px solid var(--white); border-radius: 50%; }
  .nav { position: absolute; top: 26px; left: 454px; display: flex; gap: 27px; font-size: 12.5px; font-weight: 500; color: var(--white); }
  .nav .active { color: var(--green); position: relative; }
  .nav .active::before { content: ""; position: absolute; left: 0; right: 0; top: -26px; height: 3px; background: var(--green); }
  .btn { position: absolute; background: var(--green); color: var(--white); font-size: 13px; font-weight: 500;
    display: flex; align-items: center; justify-content: center; text-transform: uppercase; }
  .hero-title { position: absolute; left: 0; width: 1200px; top: 308px; text-align: center; color: var(--white);
    font-size: 33px; line-height: 40px; }
  .hero-text { position: absolute; left: 0; width: 1200px; top: 398px; text-align: center; color: var(--white);
    font-size: 15.5px; line-height: 24px; }
  .slide-arrow { position: absolute; width: 40px; height: 40px; border-radius: 50%; background: rgba(255,255,255,0.18); }
  .hero-meta { position: absolute; top: 560px; color: var(--white); font-size: 13px; text-transform: uppercase; }
  .hero-meta b { font-weight: 700; }

  /* About */
  .about { position: absolute; left: 0; top: 640px; width: 1200px; height: 348px; overflow: hidden; background: var(--white); }
  .about-photo { position: absolute; right: 0; top: 0; width: 440px; height: 348px;
    background: linear-gradient(90deg, #ffffff 0%, #eef1f4 35%, #d9dfe6 70%, #c7d0d9 100%); }
  .section-title { position: absolute; font-size: 39px; line-height: 44px; }
  .about-text { position: absolute; left: 142px; top: 153px; width: 680px; font-size: 14.2px; line-height: 22.4px; color: var(--body-grey); }

  /* Chakras */
  .chakras { position: absolute; left: 0; top: 988px; width: 1200px; height: 729px; overflow: hidden;
    background: linear-gradient(180deg, var(--blue) 0%, #0a86de 100%); }
  .chakra { position: absolute; width: 150px; text-align: center; color: var(--white); font-weight: 700; font-size: 15px; line-height: 18px; }
  .chakra-symbol { width: 114px; height: 114px; margin: 0 auto 10px; border-radius: 50%;
    border: 2.5px solid var(--white); background: var(--symbol-fill); }
  .chakra-photo-frame { position: absolute; left: 894px; top: 454px; width: 176px; height: 179px; background: var(--white); }
  .chakra-photo { position: absolute; left: 622px; top: 95px; width: 433px; height: 520px;
    background: linear-gradient(160deg, #f4f1ee 0%, #e6ddd6 45%, #b9877f 80%, #9b4a55 100%); }

  /* Lessons */
  .lessons { position: absolute; left: 0; top: 1717px; width: 1200px; height: 607px; background: var(--white); }
  .lesson { position: absolute; top: 214px; width: 292px; }
  .lesson-box { height: 143px; border: 2.5px solid var(--green); display: flex; align-items: flex-start; justify-content: center;
    padding: 40px 22px 0; text-align: center; font-family: "Poppins", sans-serif; font-size: 18px; line-height: 24px; color: #222; }
  .lesson-num { position: absolute; left: 116px; top: -30px; width: 60px; height: 60px; border-radius: 50%; background: var(--green);
    color: var(--white); font-family: "Poppins", sans-serif; font-size: 20px; display: flex; align-items: center; justify-content: center; }
  .lesson-photo { height: 145px; }

  /* Contact */
  .contact { position: absolute; left: 0; top: 2324px; width: 1200px; height: 561px; overflow: hidden; background: var(--green-band); color: var(--white); }
  .contact-item { position: absolute; left: 142px; display: flex; align-items: center; gap: 16px; }
  .contact-icon { width: 68px; height: 68px; border-radius: 50%; background: var(--white); display: flex; align-items: center; justify-content: center; }
  .contact-label { font-size: 19px; line-height: 24px; }
  .contact-value { font-size: 25px; line-height: 32px; font-weight: 700; }
  .follow { position: absolute; left: 142px; top: 434px; font-size: 19px; display: flex; align-items: center; gap: 16px; }
  .follow span.net { font-size: 13px; font-weight: 500; }
  .field { position: absolute; left: 626px; width: 431px; border: 2px solid var(--white); color: var(--white); font-size: 14px; padding: 19px 19px; }
  .submit { position: absolute; left: 627px; top: 2743px; width: 118px; height: 38px; background: var(--white); color: var(--ink);
    font-size: 13px; font-weight: 700; display: flex; align-items: center; justify-content: center; text-transform: uppercase; }

  /* Map */
  .map { position: absolute; left: 0; top: 2885px; width: 1200px; height: 417px;
    background: linear-gradient(100deg, var(--map-green) 0%, var(--map-light) 45%, var(--map-green) 100%); }
  .map-label { position: absolute; left: 486px; top: 196px; width: 228px; height: 48px; background: var(--white);
    display: flex; align-items: center; justify-content: center; font-size: 15px; font-weight: 500; color: var(--ink); }

  .footer { position: absolute; left: 0; top: 3302px; width: 1200px; height: 84px; background: var(--footer); color: var(--white);
    display: flex; align-items: center; justify-content: center; font-size: 15px; }
</style>
</head>
<body>

<header class="hero">
  <div class="hero-photo" role="img" aria-label="Meditating figure seated before a glowing cosmic backdrop"></div>
  <div class="brand"><span class="brand-dot"></span>LON VARICK</div>
  <nav class="nav">
    <span class="active">HOME</span><span>ABOUT</span><span>SERVICES</span><span>LESSON</span><span>BLOG</span><span>CONTACT</span>
  </nav>
  <div class="btn" style="left:940px;top:16px;width:117px;height:37px;">Get a quote</div>

  <div class="slide-arrow" style="left:102px;top:310px;">
    <svg width="40" height="40" viewBox="0 0 40 40"><path d="M22 14l-6 6 6 6" fill="none" stroke="#fff" stroke-width="2"/></svg>
  </div>
  <div class="slide-arrow" style="left:1055px;top:310px;">
    <svg width="40" height="40" viewBox="0 0 40 40"><path d="M18 14l6 6-6 6" fill="none" stroke="#fff" stroke-width="2"/></svg>
  </div>

  <h1 class="hero-title heading">Kesto by Lon Varick – The Girl<br>Who Painted Her Sky</h1>
  <p class="hero-text">Lorem ipsum dolor sit amet, consectetur adipiscing elit, sed do<br>tempor incididunt ut labore et dolore magna aliqua.</p>
  <div class="btn" style="left:541px;top:459px;width:118px;height:38px;">Get started</div>

  <div class="hero-meta" style="left:142px;"><b>Client:</b> Pebble Lantern Education</div>
  <div class="hero-meta" style="right:143px;"><b>Course price:</b> AUD 4999</div>

  <svg class="abs" style="left:572px;top:606px;" width="56" height="34" viewBox="0 0 56 34">
    <path d="M0 14 L28 0 L56 14 L56 34 L0 34 Z" fill="#fff"/>
    <path d="M28 12v16M22 22l6 6 6-6" fill="none" stroke="#222" stroke-width="1.6"/>
  </svg>
</header>

<section class="about">
  <div class="about-photo" role="img" aria-label="Dandelion seed head with seeds drifting in the wind"></div>
  <h2 class="section-title heading" style="left:142px;top:80px;">About the company</h2>
  <span class="dots" style="left:142px;top:135px;color:var(--blue);"></span>
  <p class="about-text">Lorem ipsum dolor sit amet, consectetur adipiscing elit, sed do eiusmod tempor incididunt ut labore et dolore magna aliqua. Ut enim ad minim veniam, quis nostrud exercitation ullamco laboris nisi ut aliquip ex ea commodo consequat. Duis aute irure dolor in reprehenderit in voluptate velit esse cillum dolore eu fugiat nulla pariatur. Excepteur sint occaecat cupidatat non proident, sunt in culpa qui officia deserunt mollit anim id est laborum.</p>
</section>

<section class="chakras">
  <svg class="abs" style="left:1040px;top:14px;" width="116" height="116"><circle cx="58" cy="58" r="58" fill="#3aa6f0" opacity="0.55"/></svg>
  <svg class="abs" style="left:920px;top:420px;" width="340" height="340"><circle cx="170" cy="170" r="170" fill="#0a7fd6" opacity="0.6"/></svg>
  <h2 class="section-title heading" style="left:142px;top:85px;color:var(--white);">7 Chakras</h2>
  <span class="dots" style="left:142px;top:141px;color:var(--white);"></span>

  <div class="chakra" style="left:125px;top:167px;">
    <div class="chakra-symbol" role="img" aria-label="Muladhara root chakra symbol"></div>Muladhara
  </div>
  <div class="chakra" style="left:281px;top:167px;">
    <div class="chakra-symbol" role="img" aria-label="Svadhisthana sacral chakra symbol"></div>Svadhisthana
  </div>
  <div class="chakra" style="left:438px;top:167px;">
    <div class="chakra-symbol" role="img" aria-label="Manipura solar plexus chakra symbol"></div>Manipura
  </div>
  <div class="chakra" style="left:125px;top:327px;">
    <div class="chakra-symbol" role="img" aria-label="Anahata heart chakra symbol"></div>Anahata
  </div>
  <div class="chakra" style="left:281px;top:327px;">
    <div class="chakra-symbol" role="img" aria-label="Vishuddha throat chakra symbol"></div>Vishuddha
  </div>
  <div class="chakra" style="left:438px;top:327px;">
    <div class="chakra-symbol" role="img" aria-label="Ajna third eye chakra symbol"></div>Ajna
  </div>
  <div class="chakra" style="left:125px;top:487px;">
    <div class="chakra-symbol" role="img" aria-label="Sahasrara crown chakra symbol"></div>Sahasrara
  </div>

  <div class="chakra-photo-frame"></div>
  <div class="chakra-photo" role="img" aria-label="Woman meditating cross-legged on a rug with glowing chakra points along her spine"></div>
</section>

<section class="lessons">
  <h2 class="section-title heading" style="left:142px;top:82px;">Our lessons</h2>
  <span class="dots" style="left:142px;top:138px;color:var(--blue);"></span>

  <svg class="abs" style="left:56px;top:337px;" width="22" height="26" viewBox="0 0 22 26"><path d="M15 3L5 13l10 10" fill="none" stroke="#111" stroke-width="2.4"/></svg>
  <svg class="abs" style="left:1116px;top:337px;" width="22" height="26" viewBox="0 0 22 26"><path d="M7 3l10 10-10 10" fill="none" stroke="#111" stroke-width="2.4"/></svg>

  <article class="lesson" style="left:143px;">
    <div class="lesson-num">01</div>
    <div class="lesson-box">The Science of Meditation &amp; the Mind-Body Connection</div>
    <div class="lesson-photo" role="img" aria-label="Group meditating on yoga mats in a bright studio" style="background:linear-gradient(120deg,#c9a58e 0%,#e8dcd2 50%,#8aa3c4 100%);"></div>
  </article>
  <article class="lesson" style="left:454px;">
    <div class="lesson-num">02</div>
    <div class="lesson-box">Lon Varick’s Personal Healing &amp; Neuroplasticity</div>
    <div class="lesson-photo" role="img" aria-label="Person receiving energy healing while lying down" style="background:linear-gradient(120deg,#e9ecef 0%,#f6f3ef 50%,#cfd6d2 100%);"></div>
  </article>
  <article class="lesson" style="left:764px;">
    <div class="lesson-num">03</div>
    <div class="lesson-box">Emotional Stress and Disease</div>
    <div class="lesson-photo" role="img" aria-label="Woman breathing calmly outdoors in warm sunlight" style="background:linear-gradient(120deg,#d8c28c 0%,#a5a77a 50%,#6f7d5b 100%);"></div>
  </article>
</section>

<section class="contact">
  <h2 class="section-title heading" style="left:142px;top:83px;color:var(--white);">Contact us</h2>
  <span class="dots" style="left:142px;top:140px;color:var(--white);"></span>

  <div class="contact-item" style="top:171px;">
    <div class="contact-icon"><svg width="26" height="26" viewBox="0 0 24 24"><path d="M6.6 10.8a15 15 0 006.6 6.6l2.2-2.2c.3-.3.7-.4 1-.2 1.1.4 2.3.6 3.6.6.6 0 1 .4 1 1V20c0 .6-.4 1-1 1A17 17 0 013 4c0-.6.4-1 1-1h3.5c.6 0 1 .4 1 1 0 1.3.2 2.5.6 3.6.1.3 0 .7-.2 1z" fill="var(--green)"/></svg></div>
    <div><div class="contact-label">Phone:</div><div class="contact-value">+1 555 010 2040</div></div>
  </div>
  <div class="contact-item" style="top:255px;">
    <div class="contact-icon"><svg width="28" height="22" viewBox="0 0 28 22"><rect x="1" y="1" width="26" height="20" rx="2" fill="var(--green)"/><path d="M2 3l12 9 12-9" fill="none" stroke="#fff" stroke-width="2"/></svg></div>
    <div><div class="contact-label">Email:</div><div class="contact-value">hello@kestocourse.com</div></div>
  </div>
  <div class="contact-item" style="top:336px;">
    <div class="contact-icon"><svg width="18" height="26" viewBox="0 0 18 26"><path d="M9 0a9 9 0 00-9 9c0 7 9 17 9 17s9-10 9-17a9 9 0 00-9-9z" fill="var(--green)"/><circle cx="9" cy="9" r="3.2" fill="#fff"/></svg></div>
    <div><div class="contact-label">Address:</div><div class="contact-value">123, Lorem ipsum dolor sit</div></div>
  </div>
  <div class="follow">Follow Us : <span class="net">Circlet</span><span class="net">Lensly</span><span class="net">Vidora</span></div>
</section>

<div class="field" style="top:2410px;height:56px;">Your name</div>
<div class="field" style="top:2481px;height:56px;">Your email</div>
<div class="field" style="top:2551px;height:175px;">Your message</div>
<div class="submit">Submit now</div>

<section class="map" role="img" aria-label="Road map of the central and western United States">
  <div class="map-label">123, Lorem ipsum dolor sit</div>
  <svg class="abs" style="left:580px;top:246px;" width="40" height="40" viewBox="0 0 40 40"><circle cx="20" cy="20" r="19" fill="#3aa0f2"/><path d="M12 12l8 16 8-16" fill="none" stroke="#fff" stroke-width="3"/></svg>
</section>

<footer class="footer">Copyright © 2025 Lon Varick &nbsp; | &nbsp; All Rights Reserved</footer>

</body>
</html>
```